IT Company requires new Business Card design.

Over the years we have had a few different business card designs. We are now due for new cards across the board for all staff. We felt this would be a good time to start fresh with a new design. Our traditional card simply had our details on the front, and a list of services on the back. We don't particularly need the list of services, we have had cards where the only thing on the rear of the card was our logo.
Feel free to be creative, we would like our tag line "Complete IT Management" to appear at some point, doesn't necessarily have to be with the logo.
I have attached samples and drafts of various previous cards we have used over the years.

```html
<!DOCTYPE html>
<html lang="en">
<head>
<meta charset="utf-8">
<title>Kestrel Networks – Business Card</title>
<link rel="stylesheet" href="https://fonts.googleapis.com/css2?family=Arimo:wght@700&family=PT+Sans:wght@400;700&display=swap">
<style>
  :root {
    --backdrop: #e6e3df;
    --card: #ffffff;
    --slate: #5e717e;
    --band: #627784;
    --ink: #3e4850;
    --rule: #8a99a3;
    --on-band: #ffffff;
  }
  * { margin: 0; padding: 0; box-sizing: border-box; }
  html, body { width: 1200px; height: 992px; overflow: hidden; }
  body { background: var(--backdrop); position: relative; font-family: "PT Sans", sans-serif; color: var(--ink); }

  .card {
    position: absolute; top: 50px; width: 503px; height: 877px;
    background: var(--card); box-shadow: 0 2px 6px rgba(0,0,0,.18);
  }
  .card--front { left: 79px; }
  .card--back { left: 622px; }

  /* Front */
  .brand { position: absolute; left: 55px; top: 290px; display: flex; align-items: center; gap: 22px; }
  .brand__square { width: 92px; height: 92px; background: var(--slate); }
  .brand__name {
    font-family: "Arimo", sans-serif; font-weight: 700; color: var(--slate);
    font-size: 42px; line-height: 44px; text-transform: uppercase;
  }

  .name-band { position: absolute; left: 0; right: 0; top: 532px; }
  .name-band__rule { height: 3px; background: var(--rule); }
  .name-band__bar {
    margin: 5px 0; height: 87px; background: var(--band); color: var(--on-band);
    display: flex; align-items: center; justify-content: center; gap: 8px;
  }
  .name-band__person { font-weight: 700; font-size: 25px; }
  .name-band__role { font-size: 21px; }

  .contacts { position: absolute; left: 0; right: 0; top: 665px; text-align: center; font-size: 22px; line-height: 36px; }
  .contacts__row { display: flex; justify-content: center; align-items: center; gap: 10px; }
  .contacts__item { display: inline-flex; align-items: center; gap: 8px; }
  .icon { width: 20px; height: 20px; fill: var(--ink); }
  .address { position: absolute; left: 0; right: 0; top: 824px; text-align: center; font-size: 22px; }

  /* Back */
  .wordmark { position: absolute; left: 66px; top: 358px; font-family: "Arimo", sans-serif; font-weight: 700; color: var(--slate); text-transform: uppercase; }
  .wordmark__line1 { font-size: 86px; line-height: 86px; letter-spacing: 1px; }
  .wordmark__line2 { font-size: 58px; line-height: 62px; letter-spacing: 1px; }
  .tagline { position: absolute; left: 70px; top: 504px; font-size: 20px; letter-spacing: 4.6px; text-transform: uppercase; color: var(--ink); }
  .web { position: absolute; left: 0; right: 0; top: 822px; text-align: center; font-size: 23px; letter-spacing: 2.4px; color: var(--ink); }
</style>
</head>
<body>

<section class="card card--front">
  <div class="brand">
    <div class="brand__square"></div>
    <div class="brand__name">Kestrel<br>Networks</div>
  </div>

  <div class="name-band">
    <div class="name-band__rule"></div>
    <div class="name-band__bar">
      <span class="name-band__person">Daniel Hart,</span>
      <span class="name-band__role">Operation Manager</span>
    </div>
    <div class="name-band__rule"></div>
  </div>

  <div class="contacts">
    <div class="contacts__row">
      <span class="contacts__item">
        <svg class="icon" viewBox="0 0 20 20"><path d="M5 2l3 4-2 2c1 2.5 3.5 5 6 6l2-2 4 3-2 3C9 18 2 11 2 4z"/></svg>08 9555 0143
      </span>
      <span class="contacts__item">
        <svg class="icon" viewBox="0 0 20 20"><rect x="5" y="1" width="10" height="18" rx="2"/><rect x="7" y="3.5" width="6" height="6" fill="#fff"/></svg>0400 555 718
      </span>
    </div>
    <div class="contacts__row">
      <span class="contacts__item">
        <svg class="icon" viewBox="0 0 20 20"><rect x="5" y="2" width="10" height="6"/><rect x="1" y="8" width="18" height="7" rx="1"/><rect x="5" y="13" width="10" height="5"/></svg>08 9555 0143
      </span>
    </div>
    <div class="contacts__row">
      <span class="contacts__item">
        <svg class="icon" viewBox="0 0 20 20"><path d="M1 8l9-6 9 6v10H1z"/><path d="M2 8l8 5 8-5" fill="none" stroke="#fff" stroke-width="1.5"/></svg>daniel@kestrelnetworks.com.au
      </span>
    </div>
    <div class="contacts__row">
      <span class="contacts__item">
        <svg class="icon" viewBox="0 0 20 20"><circle cx="10" cy="10" r="9"/><path d="M1 10h18M10 1v18M10 1c-5 5-5 13 0 18M10 1c5 5 5 13 0 18" fill="none" stroke="#fff" stroke-width="1.2"/></svg>www.kestrelnetworks.com.au
      </span>
    </div>
  </div>

  <p class="address">Unit 4 12 Halyard Way, Lakeview WA 6100</p>
</section>

<section class="card card--back">
  <div class="wordmark">
    <div class="wordmark__line1">Kestrel</div>
    <div class="wordmark__line2">Networks</div>
  </div>
  <p class="tagline">Complete IT Management</p>
  <p class="web">www.kestrelnetworks.com.au</p>
</section>

</body>
</html>
```